landscaping core flute signs

I need core flutes created with business name and a few extra dot points for putting on fences for job sites 120cm x 120cm approx.
I want our old ones information with the new L logo and colour palette

```html
<!DOCTYPE html>
<html lang="en">
<head>
<meta charset="utf-8">
<title>Terraform Yards – Fence Sign</title>
<link rel="stylesheet" href="https://fonts.googleapis.com/css2?family=Poppins:wght@600;700;800&display=swap">
<style>
  :root {
    --backdrop: #555555;
    --sign-white: #ffffff;
    --brand-green: #5f8f58;
    --ink: #000000;
  }
  * { margin: 0; padding: 0; box-sizing: border-box; }
  html, body {
    width: 671px; height: 1200px; overflow: hidden;
    background: var(--backdrop);
    font-family: "Poppins", sans-serif;
  }
  .sign {
    position: absolute; left: 104px; top: 369px;
    width: 462px; height: 462px;
    background: var(--sign-white);
    box-shadow: 0 2px 6px rgba(0,0,0,.35);
    overflow: hidden;
  }
  .brand-mark {
    position: absolute; left: 184px; top: 22px;
    width: 94px; height: 94px; border-radius: 50%;
    background: var(--brand-green);
  }
  .brand-name {
    position: absolute; left: 0; right: 0; top: 128px;
    text-align: center; font-weight: 700; font-size: 30px;
    letter-spacing: 1px; color: var(--ink); line-height: 1;
  }
  .services {
    position: absolute; left: 20px; top: 216px;
    width: 423px; height: 76px;
    display: flex; gap: 1px;
  }
  .service {
    position: relative; flex: 1;
    background: var(--ink); color: var(--sign-white);
    border-radius: 5px;
    display: flex; align-items: center; justify-content: center;
    text-align: center; font-weight: 700; font-size: 18px; line-height: 1.25;
    padding-top: 4px;
  }
  .service--green { background: var(--brand-green); }
  .service .tick {
    position: absolute; left: 50%; top: -19px; transform: translateX(-50%);
    width: 30px; height: 30px;
  }
  .phone {
    position: absolute; left: 21px; top: 316px;
    display: flex; align-items: center; gap: 11px;
  }
  .phone-icon { width: 45px; height: 45px; }
  .phone-number {
    font-weight: 800; font-size: 57px; letter-spacing: -2px;
    color: var(--ink); line-height: 1;
  }
  .contact-band {
    position: absolute; left: 0; bottom: 0; width: 462px; height: 75px;
    background: var(--brand-green);
  }
  .email {
    position: absolute; left: 21px; top: 10px;
    display: flex; align-items: center; gap: 10px;
  }
  .email-icon { width: 24px; height: 20px; }
  .email-address {
    font-weight: 700; font-size: 29px; color: var(--sign-white);
    letter-spacing: -0.3px; line-height: 1;
  }
  .licence-tab {
    position: absolute; left: 136px; bottom: 0; width: 186px; height: 25px;
  }
  .licence-text {
    position: absolute; left: 136px; bottom: 3px; width: 186px;
    text-align: center; color: var(--sign-white);
    font-weight: 700; font-size: 11px; letter-spacing: 3px;
  }
</style>
</head>
<body>
  <main class="sign">
    <div class="brand-mark" aria-hidden="true"></div>
    <h1 class="brand-name">TERRAFORM YARDS</h1>

    <ul class="services" style="list-style:none">
      <li class="service">
        <svg class="tick" viewBox="0 0 30 30" aria-hidden="true"><circle cx="15" cy="15" r="14" fill="#5f8f58" stroke="#fff" stroke-width="2"/><path d="M8.5 15.5l4.5 4.5 8.5-9" fill="none" stroke="#fff" stroke-width="3.2" stroke-linecap="round" stroke-linejoin="round"/></svg>
        Paving &amp;<br>Concreting
      </li>
      <li class="service service--green">
        <svg class="tick" viewBox="0 0 30 30" aria-hidden="true"><circle cx="15" cy="15" r="14" fill="#000" stroke="#fff" stroke-width="2"/><path d="M8.5 15.5l4.5 4.5 8.5-9" fill="none" stroke="#fff" stroke-width="3.2" stroke-linecap="round" stroke-linejoin="round"/></svg>
        Fencing &amp;<br>Retaining
      </li>
      <li class="service">
        <svg class="tick" viewBox="0 0 30 30" aria-hidden="true"><circle cx="15" cy="15" r="14" fill="#5f8f58" stroke="#fff" stroke-width="2"/><path d="M8.5 15.5l4.5 4.5 8.5-9" fill="none" stroke="#fff" stroke-width="3.2" stroke-linecap="round" stroke-linejoin="round"/></svg>
        Design &amp;<br>Construct
      </li>
    </ul>

    <div class="phone">
      <svg class="phone-icon" viewBox="0 0 46 46" aria-hidden="true">
        <circle cx="23" cy="23" r="23" fill="#5f8f58"/>
        <path d="M15 13c1.5-1.2 3-1 3.8.4l2 3.5c.6 1.1.3 2.2-.7 2.9l-1.3.9c1 2.6 2.8 4.6 5.4 5.9l1-1.2c.8-1 2-1.2 3-.5l3.4 2.2c1.3.9 1.4 2.4.2 3.8l-1.2 1.3c-1.3 1.3-3.3 1.6-5.4.7-5.5-2.4-9.7-6.8-11.8-12.3-.8-2.2-.4-4.3 1-5.6z" fill="#fff"/>
        <path d="M26 13.5a7 7 0 0 1 6.5 6.5M26 9.5a11 11 0 0 1 10.5 10.5" fill="none" stroke="#fff" stroke-width="1.8" stroke-linecap="round"/>
      </svg>
      <span class="phone-number">0412 555 308</span>
    </div>

    <footer class="contact-band">
      <div class="email">
        <svg class="email-icon" viewBox="0 0 24 20" aria-hidden="true"><rect x="0" y="0" width="24" height="20" rx="3" fill="#000"/><path d="M4 5l8 6 8-6" fill="none" stroke="#5f8f58" stroke-width="2" stroke-linecap="round" stroke-linejoin="round"/></svg>
        <span class="email-address">sam@terraformyards.com</span>
      </div>
      <svg class="licence-tab" viewBox="0 0 186 25" aria-hidden="true"><path d="M0 25 C8 25 10 4 24 1 L162 1 C176 4 178 25 186 25 Z" fill="#000"/></svg>
      <span class="licence-text">QBSA: 1098342</span>
    </footer>
  </main>
</body>
</html>
```